Used Semi Truck Website Redesign

We are redoing the website backend and would like to also do a front end redesign. I would like a Mobile and Desktop mockup for each page. The website has more mobile visitors than desktop visitors. Our competitor is http://www.haulwaybazaar.example. We don't want to copy them exactly but we want a site that looks more like that. We need the functionality of that site. One big difference is that we also sell parts and trailers.

We need a redesign for front page, product detail page, search result page, content page. It is very important that the site is very easy to use on mobile devices. Our target audience is Truck drivers.

Feel free to use demo fonts stock images, and icons. We will purchase necessary 3rd party media when a winner is chosen.

Target Market(s)

People who want to buy used trucks.

Coding

Coded - Design and coding required

Number of Pages Required

5+ page

Requirements
Must have
• Mockup for Desktop and Mobile pages.

```html
<!DOCTYPE html>
<html lang="en">
<head>
<meta charset="utf-8">
<title>RDX Trucks – Used Trucks, Parts &amp; Trailers</title>
<link href="https://fonts.googleapis.com/css2?family=Ubuntu:wght@400;500;700&family=Lato:wght@400;700&display=swap" rel="stylesheet">
<style>
:root{
  --yellow:#f5c518;
  --yellow-dark:#e6b00e;
  --gold:#d9a91a;
  --ink:#333333;
  --ink-soft:#555555;
  --dark-btn:#3c3c3c;
  --band:#e6e6e6;
  --strip:#efefef;
  --card:#f4f4f4;
  --card-head:#ececec;
  --line:#d6d6d6;
  --white:#ffffff;
  --ad-grey:#a9a9a9;
  --ad-red:#c7350f;
}
*{box-sizing:border-box;margin:0;padding:0}
html,body{width:917px;height:1200px;overflow:hidden;background:var(--white)}
body{position:relative;font-family:"Lato",sans-serif;color:var(--ink)}
.abs{position:absolute}
h1,h2,h3,.brand{font-family:"Ubuntu",sans-serif;font-weight:500}

/* header */
.brand{left:130px;top:15px;font-size:22px;font-weight:700;letter-spacing:.3px;color:var(--ink)}
.nav-btn{top:17px;height:20px;width:61px;font:700 8px/20px "Lato",sans-serif;text-align:center;color:var(--white);background:var(--dark-btn);box-shadow:0 2px 0 #999}
.nav-btn.find{left:488px;background:var(--yellow);color:var(--ink)}
.nav-btn.sell{left:552px}
.nav-btn.research{left:615px}
.social{top:17px;width:20px;height:20px;border-radius:50%}
.s1{left:697px;background:#2b4a8b}.s2{left:721px;background:#2aa2e0}.s3{left:745px;background:#e0322e}.s4{left:769px;background:#b3873c}

.strip{left:0;top:49px;width:917px;height:21px;background:var(--strip)}
.tagline{left:130px;top:53px;font:700 10px "Ubuntu",sans-serif;color:var(--gold)}
.top-links{right:141px;top:55px;font-size:8px;color:var(--ink-soft)}
.top-links span{margin:0 6px}

/* search */
.search-band{left:0;top:70px;width:917px;height:145px;background:var(--band)}
.search-title{left:232px;top:83px;font-size:15px;color:#666;font-weight:400}
.field{width:147px;height:21px;background:var(--white);border:1px solid #cfcfcf;font-size:7.5px;line-height:19px;padding-left:10px;color:#555}
.search-btn{left:620px;top:173px;width:69px;height:21px;background:var(--yellow);font:500 10px/21px "Ubuntu",sans-serif;text-align:center;color:var(--ink);box-shadow:0 2px 0 var(--yellow-dark)}

/* category cards */
.card{width:272px;height:178px;background:var(--card);border:1px solid #e2e2e2;box-shadow:0 3px 3px -2px #ccc}
.card-head{height:30px;background:linear-gradient(var(--white),var(--card-head));padding:8px 14px;font:400 14px "Ubuntu",sans-serif;color:#555}
.card-q{position:absolute;left:15px;top:37px;font-size:7.5px;color:var(--ink)}
.card-art{position:absolute;left:15px;top:57px;width:76px;height:76px;border-radius:50%;background:linear-gradient(135deg,#f7cf2e,#f0b80c)}
.card-list{position:absolute;left:108px;top:62px;list-style:none;font-size:7.5px;line-height:13px}
.card-list li::before{content:"";display:inline-block;border-left:4px solid var(--yellow);border-top:3px solid transparent;border-bottom:3px solid transparent;margin-right:11px}
.card-btn{position:absolute;left:16px;top:162px;width:167px;height:19px;font:500 9px/19px "Ubuntu",sans-serif;text-align:center;color:var(--white);background:var(--dark-btn)}
.card-btn.yellow{background:var(--yellow);color:var(--ink)}

/* makes & dealer */
.makes-band{left:0;top:650px;width:917px;height:214px;background:var(--strip)}
.section-title{font-size:12px;color:var(--ink)}
.makes{left:179px;top:697px;display:grid;grid-template-columns:110px 76px 80px;row-gap:11.4px;font-size:8px}
.divider{left:458px;top:660px;width:1px;height:194px;background:var(--line)}
.locate-btn{left:657px;top:665px;width:68px;height:20px;background:var(--yellow);font:700 7.5px/20px "Lato",sans-serif;text-align:center;color:var(--ink)}
.world-map{left:505px;top:698px;width:237px;height:130px;background:radial-gradient(ellipse at 50% 50%,#cfcfcf,#e6e6e6 75%);border-radius:40%}

/* ad & about */
.ad{left:178px;top:883px;width:269px;height:184px;background:linear-gradient(100deg,var(--ad-grey) 45%,var(--ad-red) 46%)}
.about-title{left:487px;top:889px;font-size:13px}
.about-text{left:487px;top:914px;width:247px;font-size:7.5px;line-height:17.2px;text-align:justify}
.read-more{left:487px;top:1046px;font-size:7.5px;font-weight:700}

/* footer */
.footer{left:0;top:1094px;width:917px;height:74px;background:#f1f1f1}
.footer-text{left:140px;top:1104px;width:637px;text-align:center;font-size:8px;line-height:15px;color:var(--ink-soft)}
.footer-links{left:0;top:1143px;width:917px;text-align:center;font-size:8px;color:var(--ink-soft)}
.copyright-bar{left:0;top:1168px;width:917px;height:32px;background:#e6e6e6;text-align:center;font-size:7.5px;line-height:32px;color:var(--ink-soft)}
</style>
</head>
<body>

<header>
  <div class="abs brand">RDX <span style="color:var(--ink)">TRUCKS</span></div>
  <nav>
    <div class="abs nav-btn find">FIND</div>
    <div class="abs nav-btn sell">SELL</div>
    <div class="abs nav-btn research">RESEARCH</div>
  </nav>
  <div class="abs social s1" aria-label="Social link"></div>
  <div class="abs social s2" aria-label="Social link"></div>
  <div class="abs social s3" aria-label="Social link"></div>
  <div class="abs social s4" aria-label="Social link"></div>
  <div class="abs strip"></div>
  <div class="abs tagline">200,000 00 We sell used trucks &amp; also parts, trailers etc.</div>
  <div class="abs top-links">MyTrader<span>|</span>Login<span>|</span>Register<span>|</span>Find a Dealer<span>|</span>Dealer Login</div>
</header>

<section class="abs search-band"></section>
<h2 class="abs search-title">Quick Search</h2>
<div class="abs field" style="left:231px;top:112px">Key word</div>
<div class="abs field" style="left:386px;top:112px">Select a Class</div>
<div class="abs field" style="left:542px;top:112px">Select a Category</div>
<div class="abs field" style="left:231px;top:141px">Select a Make</div>
<div class="abs field" style="left:386px;top:141px">Zip Code</div>
<div class="abs field" style="left:542px;top:141px">Any Distane</div>
<div class="abs search-btn">Search</div>

<article class="abs card" style="left:182px;top:232px">
  <div class="card-head">Find Heavy Duty Trucks For Sale</div>
  <p class="card-q">What Type Heavy Duty Truck do you need?</p>
  <div class="card-art" role="img" aria-label="Dump truck icon on yellow circle"></div>
  <ul class="card-list"><li>Cab-Chassis</li><li>Flatbed-Truck</li><li>Box Truck-Straight Truck</li><li>Day Cab</li><li>Tractor</li><li>Crane Truck</li><li>Bucket Truck - Boom Truck</li></ul>
  <div class="card-btn yellow">See all Heavy Duty Trucks</div>
</article>

<article class="abs card" style="left:463px;top:232px">
  <div class="card-head">Find Medium Duty Trucks For Sale</div>
  <p class="card-q">What Type of Medium Duty Truck do you need?</p>
  <div class="card-art" role="img" aria-label="Tow truck icon on yellow circle"></div>
  <ul class="card-list"><li>Rollback Tow Truck</li><li>Utility Truck - Service Truck</li><li>Crew Cab</li><li>Refrigerated Truck</li><li>Wrecker Tow Truck</li><li>Bucket Truck - Boom Truck</li><li>Flatbed</li></ul>
  <div class="card-btn">See all Medium Duty Trucks</div>
</article>

<article class="abs card" style="left:182px;top:428px">
  <div class="card-head">Find Light Duty Trucks For Sale</div>
  <p class="card-q">What Type of Light Duty Truck do you need?</p>
  <div class="card-art" role="img" aria-label="Box truck icon on yellow circle"></div>
  <ul class="card-list"><li>Dump Truck</li><li>Crew Cab</li><li>Flatbed Truck</li><li>Van</li><li>Passenger Van</li><li>Cutaway-Cube Van</li><li>Refrigerated Truck</li></ul>
  <div class="card-btn">See all Light Duty Trucks</div>
</article>

<article class="abs card" style="left:463px;top:428px">
  <div class="card-head">Find Truck Trailers For Sale</div>
  <p class="card-q">What Type of Trailer do you need?</p>
  <div class="card-art" role="img" aria-label="Trailer icon on yellow circle"></div>
  <ul class="card-list"><li>Rollback Tow Truck</li><li>Utility Truck - Service Truck</li><li>Crew Cab</li><li>Refrigerated Truck</li><li>Wrecker Tow Truck</li><li>Bucket Truck - Boom Truck</li><li>Flatbed</li></ul>
  <div class="card-btn">See all Truck Trailers</div>
</article>

<section class="abs makes-band"></section>
<h3 class="abs section-title" style="left:179px;top:668px">Trucks for sale by Make</h3>
<div class="abs makes">
  <span>Fenwick</span><span>Rook</span><span>Hanto</span>
  <span>Freightway</span><span>Gvx</span><span>Stirlane</span>
  <span>Cheval</span><span>Izaro</span><span>Meridan-Berg</span>
  <span>Petermark</span><span>Mardo</span><span>Nolan</span>
  <span>Intermotive</span><span>Valdo</span><span></span>
  <span>Kenmoor</span><span>Dalton</span><span></span>
</div>
<div class="abs divider"></div>
<h3 class="abs section-title" style="left:489px;top:668px">Find a Dealer</h3>
<div class="abs locate-btn">Find Location</div>
<div class="abs world-map" role="img" aria-label="Dotted world map with dealer location pins"></div>

<div class="abs ad" role="img" aria-label="CraftLine advertisement: worker with power tool, heavy industrial direct-hire contractor"></div>
<h3 class="abs section-title about-title">RDX Trucks</h3>
<p class="abs about-text">Sed ut perspiciatis unde omnis iste natus error sit voluptatem accusantium doloremque laudantium, totam rem aperiam, eaque ipsa quae ab illo inventore veritatis et quasi architecto beatae vitae dicta sunt explicabo. Nemo enim ipsam voluptatem quia voluptas sit aspernatur aut odit aut fugit, sed quia consequuntur magni dolores eos qui ratione voluptatem sequi nesciunt. Neque porro quisquam est, qui dolorem ipsum quia dolor sit amet,</p>
<div class="abs read-more">Read more ....</div>

<footer>
  <div class="abs footer"></div>
  <p class="abs footer-text">Ut enim ad minima veniam, quis nostrum exercitationem ullam corporis suscipit laboriosam, nisi ut aliquid ex ea commodi consequatur Quis autem vel eum iure reprehenderit qui in ea voluptate velit esse quam nihil molestiae consequatur, vel illum qui dolorem eum fugiat quo voluptas nulla pariatur</p>
  <div class="abs footer-links">Security Center|Advertiser Agreement|Community Guidelines|Copyright|Privacy Policy|Terms of Use</div>
  <div class="abs copyright-bar">Copyrights © 2016,www.sitename.com. All Rights Reserved.</div>
</footer>

</body>
</html>
```